gtw school poster design and change logo name

We already have a logo which only needs to be slightly modified with "school".
We also have two advertising faces, a girl and a boy, which should be on our poster.
Important key data:

bilingual D/E small classes
daycare
private kindergarten
private school from 2024

Poster size: 268,5 x 128 cm
We need logo sizes in different sizes
also for T-shirts.
Attached also a old poster

new clients

0094D4
00A9DD
6FCCEA
C7EBF8
E9F6FB
59FF00
82FF00
B8FF75
E3FFCB
F4FFEA
FFC000
F8CF3A
FAE287
FDF2CF
FEFAEE
F0912C
F2A743
F7CA91
FBE8D2
FDF5EE

```html
<!DOCTYPE html>
<html lang="de">
<head>
<meta charset="utf-8">
<title>gtw school – Poster</title>
<link rel="stylesheet" href="https://fonts.googleapis.com/css2?family=Lilita+One&family=Poppins:wght@500;600;700&display=swap">
<style>
  :root {
    --page: #ffffff;
    --ink: #464e50;
    --orange: #f7ad00;
    --orange-deep: #f0912c;
    --lime: #bed000;
    --lime-soft: #e3f0a0;
    --pink: #e8468e;
    --blue: #00a1dc;
    --blue-light: #6fccea;
    --white: #ffffff;
  }
  * { box-sizing: border-box; margin: 0; padding: 0; }
  html, body { width: 969px; height: 1200px; overflow: hidden; background: var(--page); }
  .canvas { position: relative; width: 969px; height: 1200px; }
  .poster {
    position: absolute; left: 35px; top: 386px; width: 900px; height: 428px;
    background: var(--white); overflow: hidden;
    box-shadow: 0 6px 24px rgba(0,0,0,0.18);
    font-family: "Poppins", sans-serif;
  }
  .headline { position: absolute; left: 26px; font-family: "Lilita One", sans-serif; line-height: 1; letter-spacing: 0.5px; }
  .headline--bilingual { top: 28px; font-size: 55px; color: var(--orange); }
  .headline--classes { top: 78px; font-size: 66px; color: var(--ink); }
  .claim-band { position: absolute; left: 26px; top: 144px; width: 510px; height: 78px; }
  .claim-band svg { position: absolute; inset: 0; }
  .claim-text {
    position: absolute; left: 18px; top: 13px; width: 480px;
    color: var(--white); font-weight: 500; font-size: 17.5px; line-height: 1.25;
  }
  .school-start { position: absolute; left: 38px; top: 226px; line-height: 1; }
  .school-start__label { font-weight: 600; font-size: 17px; color: var(--ink); }
  .school-start__year { font-weight: 700; font-size: 32px; color: var(--pink); margin-top: 1px; }
  .age-range {
    position: absolute; left: 191px; top: 227px; width: 316px; height: 42px;
    background: var(--pink); border-radius: 4px 10px 10px 4px;
    color: var(--white); font-weight: 600; font-size: 13px; line-height: 1.25; padding: 5px 16px;
  }
  .contact-band { position: absolute; left: 0; top: 274px; width: 620px; height: 154px; }
  .brand { position: absolute; left: 22px; top: 344px; width: 135px; display: flex; align-items: center; gap: 6px; white-space: nowrap; }
  .brand__dot { width: 10px; height: 10px; border-radius: 50%; background: var(--white); flex: none; }
  .brand__name { font-family: "Lilita One", sans-serif; font-size: 22px; color: var(--white); line-height: 1; }
  .contact { position: absolute; left: 173px; top: 308px; color: var(--white); }
  .contact__title { font-family: "Lilita One", sans-serif; font-size: 25px; transform: skewX(-10deg); line-height: 1; margin-bottom: 8px; }
  .contact__title span { color: var(--orange); }
  .contact__row { display: flex; align-items: center; gap: 8px; line-height: 1; margin-bottom: 7px; }
  .contact__row svg { width: 14px; height: 14px; flex: none; }
  .contact__phone { font-weight: 700; font-size: 18px; }
  .contact__web { font-weight: 700; font-size: 19px; }
  .contact__address { font-weight: 500; font-size: 13.5px; }
  .photo-area {
    position: absolute; left: 540px; top: 70px; width: 360px; height: 358px;
    border-radius: 180px 0 0 0;
    background: radial-gradient(circle at 55% 55%, #f4c9a8 0%, #e9b48c 30%, #f7ad00 62%, #f0912c 100%);
  }
  .speech-cloud { position: absolute; left: 555px; top: 14px; width: 180px; height: 140px; }
  .speech-cloud__text {
    position: absolute; left: 0; top: 34px; width: 172px; text-align: center;
    font-family: "Lilita One", sans-serif; font-size: 19px; line-height: 1; color: var(--white);
    transform: skewX(-8deg);
  }
</style>
</head>
<body>
<div class="canvas">
  <div class="poster">
    <div class="photo-area" role="img" aria-label="Lachender Junge und lächelndes Mädchen mit farbig bemalten Händen vor einem orangen Sonnenkranz"></div>

    <div class="speech-cloud">
      <svg width="180" height="140" viewBox="0 0 180 140" aria-hidden="true">
        <g fill="var(--blue)">
          <circle cx="90" cy="50" r="44"/>
          <circle cx="135" cy="48" r="32"/>
          <circle cx="40" cy="75" r="36"/>
          <circle cx="90" cy="85" r="40"/>
          <circle cx="130" cy="80" r="30"/>
          <circle cx="122" cy="117" r="7"/>
          <circle cx="132" cy="130" r="4"/>
        </g>
      </svg>
      <div class="speech-cloud__text">SPRECHEN<br>SIE<br>ENGLISCH?</div>
    </div>

    <h1 class="headline headline--bilingual">BILINGUAL D/E</h1>
    <h2 class="headline headline--classes">SMALL CLASSES</h2>

    <div class="claim-band">
      <svg viewBox="0 0 510 78" preserveAspectRatio="none" aria-hidden="true">
        <path d="M14 6 Q250 -2 500 10 Q512 40 498 64 Q250 80 14 74 Q0 40 14 6Z" fill="var(--lime-soft)"/>
        <path d="M12 2 Q250 -4 494 6 Q508 34 494 58 Q250 72 12 68 Q-2 36 12 2Z" fill="var(--lime)"/>
      </svg>
      <p class="claim-text">Bei uns lernen ALLE Kinder spielend einfach in kürzester Zeit Englisch wie eine 2.Muttersprache.</p>
    </div>

    <div class="school-start">
      <div class="school-start__label">PRIVATSCHULE</div>
      <div class="school-start__year">AB 2024</div>
    </div>
    <div class="age-range">Kinderkrippe &amp; Hort Ab 3.Lebensmonat<br>bis zum 12.Lebensjahr</div>

    <svg class="contact-band" viewBox="0 0 620 154" preserveAspectRatio="none" aria-hidden="true">
      <path d="M0 22 Q140 -6 300 8 Q450 20 540 12 L540 22 Q450 28 300 16 Q140 4 0 30Z" fill="var(--blue-light)"/>
      <path d="M0 30 Q140 8 300 18 Q450 30 545 20 Q528 50 540 74 Q552 100 530 120 Q560 140 545 154 L0 154Z" fill="var(--blue)"/>
    </svg>

    <div class="brand">
      <span class="brand__dot"></span>
      <span class="brand__name">gtw school</span>
    </div>

    <div class="contact">
      <div class="contact__title"><span>CONTACT</span> US</div>
      <div class="contact__row">
        <svg viewBox="0 0 24 24" aria-hidden="true"><path fill="var(--orange)" d="M6.6 10.8a15 15 0 0 0 6.6 6.6l2.2-2.2a1 1 0 0 1 1-.25 11.4 11.4 0 0 0 3.6.57 1 1 0 0 1 1 1V20a1 1 0 0 1-1 1A17 17 0 0 1 3 4a1 1 0 0 1 1-1h3.5a1 1 0 0 1 1 1c0 1.250.2 2.450.57 3.570a1 1 0 0 1-.25 1z"/></svg>
        <span class="contact__phone">+41 790000000</span>
      </div>
      <div class="contact__row">
        <svg viewBox="0 0 24 24" aria-hidden="true"><g fill="none" stroke="var(--orange)" stroke-width="2.2"><circle cx="12" cy="12" r="9"/><path d="M3 12h18M12 3c3 3 3 15 0 18M12 3c-3 3-3 15 0 18"/></g></svg>
        <span class="contact__web">www.gtw-daycare.ch</span>
      </div>
      <div class="contact__row">
        <svg viewBox="0 0 24 24" aria-hidden="true"><path fill="var(--lime)" d="M12 2a7 7 0 0 0-7 7c0 5 7 13 7 13s7-8 7-13a7 7 0 0 0-7-7zm0 9.5A2.5 2.5 0 1 1 12 6.5a2.5 2.5 0 0 1 0 5z"/></svg>
        <span class="contact__address">Lindenweg 12 8000 Talwil</span>
      </div>
    </div>
  </div>
</div>
</body>
</html>
```